Free range pig farm business

We'd like a simple but elegant website for our new free range pig farm business.
Check out www.kelvorrahogsteads.com.au and http://www.tirrowfield.com.au/
pages:
Home
About
Shop
Contact
Target Market(s)
People who would want to find out where they could buy our pork
Industry/Entity Type
Agribusiness
Number of Pages Required
4 page
Font styles to use
Other font styles liked:
- As per our logo
Requirements
Must have
- Ability for us to update weekly with new news and photos

```html
<!DOCTYPE html>
<html lang="en">
<head>
<meta charset="utf-8">
<title>Coolabri Farm</title>
<link href="https://fonts.googleapis.com/css2?family=Open+Sans:wght@400;600;700&display=swap" rel="stylesheet">
<style>
:root{
  --green:#abc12e;
  --green-dark:#2f4a1e;
  --pale:#eceed6;
  --white:#ffffff;
  --ink:#111111;
  --muted:#8a8a8a;
  --price:#a5a5a5;
  --line:#dcdcdc;
}
*{margin:0;padding:0;box-sizing:border-box}
html,body{width:1200px;height:2632px;overflow:hidden}
body{position:relative;font-family:'Open Sans',Arial,sans-serif;background:var(--white);color:var(--ink)}
.abs{position:absolute}
.btn{position:absolute;background:var(--green);color:var(--white);font-size:11px;text-transform:uppercase;display:flex;align-items:center;justify-content:center;letter-spacing:.2px}

/* header */
.site-header{left:0;top:0;width:1200px;height:116px;background:var(--pale)}
.brand{left:158px;top:42px;display:flex;align-items:center;gap:10px}
.brand-dot{width:28px;height:28px;border-radius:50%;background:var(--green-dark)}
.brand-name{font-size:14px;font-weight:700;color:var(--green-dark);text-transform:uppercase;white-space:nowrap}
.main-nav a{position:absolute;top:42px;height:32px;line-height:32px;font-size:11.5px;font-weight:600;color:var(--ink);text-decoration:none;text-transform:uppercase}
.main-nav .active{background:var(--green);color:var(--white);border-radius:16px;width:84px;text-align:center}
.search{left:960px;top:40px;width:36px;height:36px;border-radius:50%;background:var(--green)}

/* hero */
.hero{left:0;top:116px;width:1200px;height:524px;background:radial-gradient(ellipse at 45% 50%,#7a4a36 0%,#4a2a1c 40%,#2a1a12 75%,#1a100a 100%)}
.hero-title{left:0;top:340px;width:1200px;text-align:center;color:var(--white);font-size:31px;font-weight:400;text-transform:uppercase}
.hero-sub{left:0;top:390px;width:1200px;text-align:center;color:var(--white);font-size:15px;text-transform:uppercase}

/* sections */
.band-pale{left:0;width:1200px;background:var(--pale)}
.section-title{left:0;width:1200px;text-align:center;font-size:30px;font-weight:600;text-transform:uppercase}
.photo{position:absolute}
.svc-title{position:absolute;top:1038px;font-size:15px;font-weight:700;text-transform:uppercase}
.svc-text{position:absolute;top:1078px;width:285px;font-size:11.5px;line-height:20px;color:var(--muted)}
.item-name{position:absolute;top:1672px;width:210px;font-size:16px;line-height:25px;color:var(--muted)}
.item-price{position:absolute;top:1730px;font-size:19px;color:var(--price)}
.about-text{left:205px;top:2040px;width:790px;text-align:center;font-size:14.5px;line-height:26px;color:var(--muted)}

/* footer */
.newsletter-label{left:232px;top:2363px;display:flex;align-items:center;gap:10px;font-size:15.5px}
.email-box{left:447px;top:2352px;width:521px;height:46px;border:1px solid var(--line);background:var(--white)}
.email-box span{position:absolute;left:14px;top:15px;font-size:10px;color:#aaa}
.foot-brand{left:0;top:2432px;width:1200px;display:flex;flex-direction:column;align-items:center;gap:10px}
.foot-nav a{position:absolute;top:2552px;font-size:11.5px;font-weight:600;color:var(--ink);text-decoration:none;text-transform:uppercase}
.copyright{left:0;top:2586px;width:1200px;text-align:center;font-size:11.5px;font-weight:600;text-transform:uppercase}
</style>
</head>
<body>

<header class="abs site-header">
  <div class="abs brand"><span class="brand-dot"></span><span class="brand-name">Coolabri Farm</span></div>
  <nav class="main-nav">
    <a class="active" style="left:512px">Home</a>
    <a style="left:622px">About</a>
    <a style="left:710px">Service</a>
    <a style="left:803px">Shop</a>
    <a style="left:882px">Contact</a>
  </nav>
  <div class="abs search">
    <svg width="36" height="36" viewBox="0 0 36 36"><circle cx="16.5" cy="16.5" r="5" fill="none" stroke="#fff" stroke-width="2"/><line x1="20" y1="20" x2="24" y2="24" stroke="#fff" stroke-width="2.2" stroke-linecap="round"/></svg>
  </div>
</header>

<section>
  <div class="abs hero" role="img" aria-label="Seared pork steaks with rosemary and berries in a cast iron pan on a wooden table"></div>
  <h1 class="abs hero-title">Coolabri Farm</h1>
  <p class="abs hero-sub">We are a new free range pig farm business</p>
  <a class="btn" style="left:526px;top:440px;width:148px;height:39px">Learn More</a>
</section>

<section class="abs band-pale" style="top:640px;height:684px"></section>
<h2 class="abs section-title" style="top:736px">Services</h2>
<div class="photo" style="left:144px;top:812px;width:288px;height:190px;background:linear-gradient(#c9b58a,#a88f5e)" role="img" aria-label="Piglets on straw in a pasture"></div>
<div class="photo" style="left:454px;top:812px;width:288px;height:190px;background:linear-gradient(#7fb24a,#3f7a22)" role="img" aria-label="Pink piglets on green grass"></div>
<div class="photo" style="left:768px;top:812px;width:288px;height:190px;background:linear-gradient(#a3977e,#3a3224)" role="img" aria-label="Farmer tending pigs in a dusty paddock"></div>

<h3 class="svc-title" style="left:144px">Feeding</h3>
<h3 class="svc-title" style="left:454px">Breeding</h3>
<h3 class="svc-title" style="left:768px">Care &amp; Management</h3>
<p class="svc-text" style="left:144px">Sed ut perspiciatis unde omnis iste natus error sit voluptatem accusantium doloremque laudantium, totam rem aperiam, eaque ipsa quae ab illo inventore veritatis et quasi architecto</p>
<p class="svc-text" style="left:451px">Sed ut perspiciatis unde omnis iste natus error sit voluptatem accusantium doloremque laudantium, totam rem aperiam, eaque ipsa quae ab illo inventore veritatis et quasi architecto</p>
<p class="svc-text" style="left:768px">Sed ut perspiciatis unde omnis iste natus error sit voluptatem accusantium doloremque laudantium, totam rem aperiam, eaque ipsa quae ab illo inventore veritatis et quasi architecto</p>
<a class="btn" style="left:144px;top:1175px;width:96px;height:39px">Read More</a>
<a class="btn" style="left:451px;top:1175px;width:96px;height:39px">Read More</a>
<a class="btn" style="left:768px;top:1175px;width:96px;height:39px">Read More</a>

<h2 class="abs section-title" style="top:1400px">Shop</h2>
<div class="photo" style="left:144px;top:1501px;width:210px;height:155px;background:linear-gradient(#d9a59a,#7b6a5c)" role="img" aria-label="Pigs looking through a gate"></div>
<div class="photo" style="left:377px;top:1501px;width:210px;height:155px;background:linear-gradient(#c9a89a,#5a4a3e)" role="img" aria-label="Piglets in a pen"></div>
<div class="photo" style="left:614px;top:1501px;width:210px;height:155px;background:linear-gradient(#6f86a8,#5a4f45)" role="img" aria-label="Spotted and pink pigs in a yard"></div>
<div class="photo" style="left:844px;top:1501px;width:210px;height:155px;background:linear-gradient(#cfb7a8,#4e4035)" role="img" aria-label="Young pigs on slatted flooring"></div>

<p class="item-name" style="left:144px">Sed ut perspiciatis unde omnis iste natus</p>
<p class="item-name" style="left:377px">Sed ut perspiciatis unde omnis iste natus</p>
<p class="item-name" style="left:614px">Sed ut perspiciatis unde omnis iste natus</p>
<p class="item-name" style="left:844px">Sed ut perspiciatis unde omnis iste natus</p>
<p class="item-price" style="left:140px">$25.00</p>
<p class="item-price" style="left:373px">$25.00</p>
<p class="item-price" style="left:611px">$25.00</p>
<p class="item-price" style="left:841px">$25.00</p>
<a class="btn" style="left:144px;top:1780px;width:100px;height:28px">Shop Now</a>
<a class="btn" style="left:377px;top:1780px;width:100px;height:28px">Shop Now</a>
<a class="btn" style="left:614px;top:1780px;width:100px;height:28px">Shop Now</a>
<a class="btn" style="left:844px;top:1780px;width:100px;height:28px">Shop Now</a>

<section class="abs band-pale" style="top:1903px;height:391px"></section>
<h2 class="abs section-title" style="top:1976px">About</h2>
<p class="abs about-text">Sed ut perspiciatis unde omnis iste natus error sit voluptatem accusantium doloremque laudantium, totam rem aperiam, eaque ipsa quae ab illo inventore veritatis et quasi architecto beatae vitae dicta sunt explicabo. Nemo enim ipsam voluptatem quia voluptas sit aspernatur aut odit aut fugit, sed quia consequuntur magni dolores eos qui ratione voluptatem sequi nesciunt. Neque porro quisquam est, qui dolorem</p>
<a class="btn" style="left:526px;top:2192px;width:148px;height:39px">Learn More</a>

<footer>
  <div class="abs newsletter-label">
    <svg width="20" height="15" viewBox="0 0 20 15"><rect x="1" y="1" width="18" height="13" fill="none" stroke="#abc12e" stroke-width="1.6"/><polyline points="1,1 10,8 19,1" fill="none" stroke="#abc12e" stroke-width="1.6"/></svg>
    <span>Newsletter Subscription</span>
  </div>
  <div class="abs email-box"><span>Enter Your E-mail Address</span></div>
  <a class="btn" style="left:831px;top:2360px;width:133px;height:30px">Subscribe Now</a>
  <div class="abs foot-brand"><span class="brand-dot"></span><span class="brand-name">Coolabri Farm</span></div>
  <nav class="foot-nav">
    <a style="left:400px">Home</a>
    <a style="left:482px">About</a>
    <a style="left:570px">Service</a>
    <a style="left:663px">Shop</a>
    <a style="left:744px">Contact</a>
  </nav>
  <p class="abs copyright">© 2016 Company Name &nbsp;&nbsp;| All Rights Reserved</p>
</footer>

</body>
</html>
```